Corvane Holdings , new business card design

investment firm with corporate clients . need double sided business card , vertical and horizontal options ,logo must be clear. prefer pantone colors only and sharp design. website also www.corvane.ae

Khalid Bin Tarrafi
Managing Director
Tel. +971 4 387 2940
Mobile +971 50 518 2403
khalid@corvane.ae
Q-Span Plaza, officw 18-B07, Warqa Gardens, Dubai

Contact Information for Business Card

Khalid Bin Tarrafi
Managing Director

Font styles to use
Serif

Colors

Designer to choose colors to be used in the design.

```html
<!DOCTYPE html>
<html lang="en">
<head>
<meta charset="utf-8">
<title>Corvane Holdings — Business Card</title>
<link rel="stylesheet" href="https://fonts.googleapis.com/css2?family=Raleway:wght@400;500;700&display=swap">
<style>
  :root {
    --backdrop: #ebe8e5;
    --card: #ffffff;
    --ink: #2b2d33;
    --ink-soft: #5d6068;
    --brand-blue: #4a6f98;
    --band-grey: #d9d4d1;
    --rule: #cfcfcf;
  }
  * { margin: 0; padding: 0; box-sizing: border-box; }
  html, body {
    width: 1200px; height: 997px; overflow: hidden;
    background: var(--backdrop);
    font-family: "Raleway", sans-serif;
    color: var(--ink);
  }
  .sheet {
    position: relative; width: 1200px; height: 997px;
    display: flex; flex-direction: column; align-items: center; justify-content: center; gap: 50px;
  }
  .card {
    position: relative; width: 620px; height: 354px;
    background: var(--card);
    box-shadow: 0 2px 10px rgba(0,0,0,0.08);
    overflow: hidden;
  }
  .wordmark {
    display: flex; align-items: center; gap: 10px;
    font-weight: 400; color: var(--ink);
    text-transform: uppercase; white-space: nowrap;
  }
  .wordmark__square { width: 10px; height: 10px; background: var(--brand-blue); flex: none; }

  /* information side */
  .card--info .wordmark {
    position: absolute; left: 34px; top: 150px;
    font-size: 16px; letter-spacing: 3px;
  }
  .divider {
    position: absolute; left: 318px; top: 38px; width: 1px; height: 218px;
    background: var(--rule);
  }
  .contact {
    position: absolute; left: 340px; top: 44px; width: 260px;
  }
  .contact__name { font-size: 17px; font-weight: 700; color: var(--ink); }
  .contact__title { font-size: 13px; color: var(--ink-soft); margin-top: 3px; }
  .contact__lines { list-style: none; margin-top: 22px; }
  .contact__lines li {
    display: flex; align-items: center; gap: 8px;
    font-size: 12.5px; color: var(--ink-soft); line-height: 19px;
  }
  .contact__lines svg { width: 11px; height: 11px; flex: none; }
  .contact__address { font-size: 12.5px; color: var(--ink-soft); line-height: 18px; margin-top: 18px; }
  .footer-band { position: absolute; left: 0; bottom: 0; width: 620px; height: 100px; }
  .footer-band__url {
    position: absolute; right: 44px; bottom: 62px;
    font-size: 12.5px; font-weight: 500; letter-spacing: 4px; color: var(--ink);
  }

  /* logo side */
  .card--logo { display: flex; align-items: center; justify-content: center; }
  .card--logo .wordmark { font-size: 30px; letter-spacing: 7px; gap: 16px; }
  .card--logo .wordmark__square { width: 16px; height: 16px; }
</style>
</head>
<body>
<main class="sheet">

  <section class="card card--info" aria-label="Business card, contact side">
    <div class="wordmark"><span class="wordmark__square"></span>Corvane Holdings</div>
    <div class="divider"></div>
    <div class="contact">
      <p class="contact__name">Khalid Bin Tarrafi</p>
      <p class="contact__title">Managing Director</p>
      <ul class="contact__lines">
        <li>
          <svg viewBox="0 0 12 12" aria-hidden="true"><path d="M2.5 1 L4.5 1 L5.3 3.4 L4 4.4 C4.7 6 6 7.3 7.6 8 L8.6 6.7 L11 7.5 L11 9.5 C11 10.3 10.3 11 9.5 11 C5 11 1 7 1 2.5 C1 1.7 1.7 1 2.5 1 Z" fill="var(--brand-blue)"/></svg>
          +971 4 387 2940
        </li>
        <li>
          <svg viewBox="0 0 12 12" aria-hidden="true"><rect x="3" y="0.8" width="6" height="10.4" rx="1.2" fill="none" stroke="var(--brand-blue)" stroke-width="1.2"/><circle cx="6" cy="9.2" r="0.7" fill="var(--brand-blue)"/></svg>
          +971 50 518 2403
        </li>
        <li>
          <svg viewBox="0 0 12 12" aria-hidden="true"><rect x="0.8" y="2.2" width="10.4" height="7.6" rx="1" fill="var(--brand-blue)"/><path d="M1.2 2.8 L6 6.6 L10.8 2.8" fill="none" stroke="#fff" stroke-width="1"/></svg>
          khalid@corvane.ae
        </li>
      </ul>
      <p class="contact__address">Q-Span Plaza, officw 18-B07,<br>Warqa Gardens, Dubai</p>
    </div>
    <svg class="footer-band" viewBox="0 0 620 100" aria-hidden="true">
      <polygon points="420,18 600,18 600,44 402,44" fill="var(--band-grey)"/>
      <polygon points="600,14 620,14 620,48 600,48 608,31" fill="var(--brand-blue)"/>
      <polygon points="0,44 402,44 420,18 440,18 414,58 0,58" fill="var(--brand-blue)"/>
      <rect x="0" y="44" width="414" height="32" fill="var(--brand-blue)"/>
    </svg>
    <span class="footer-band__url">www.corvane.ae</span>
  </section>

  <section class="card card--logo" aria-label="Business card, logo side">
    <div class="wordmark"><span class="wordmark__square"></span>Corvane Holdings</div>
  </section>

</main>
</body>
</html>
```